Business card for my new company (Accounting firm)

I need a business card for my new business Brightwell Advisory and Ledger SA. Our services are accounting, tax, audit and financial management. Our customers are small companies, start-ups and new companies. The final design has to show financial security, trust and growth. Please find our logo attached to the business card. Text for the business card: Brightwell Advisory and Ledger SA Tomas Varenholt Director and Founder Certified Accountant Tel. 022 418 57 34 tv@clairevalconseil.ch www.clairevalconseil.ch Rue des Vergières 27 1201 Geneva
Target Market(s)
Our customers are small companies, start-ups and new companies.
Industry/Entity Type
Finance And Accounting
Contact Information for Business Card
Claireval Conseil et Comptes SA
Tomas Varenholt
Directeur et Fondateur
Expert-comptable diplômé
Tél. 022 418 57 34
tv@clairevalconseil.ch
www.clairevalconseil.ch
Rue des Vergières 27
1201 Genève

```html
<!DOCTYPE html>
<html lang="en">
<head>
<meta charset="utf-8">
<title>Claireval Conseil et Comptes – Business Card</title>
<link rel="stylesheet" href="https://fonts.googleapis.com/css2?family=Lato:wght@400;700;900&display=swap">
<style>
  :root {
    --stage: #2f2f30;
    --paper: #ffffff;
    --navy: #1b5f98;
    --blue: #2585c6;
    --sky: #33ade2;
    --ink: #3a3d42;
  }
  * { margin: 0; padding: 0; box-sizing: border-box; }
  html, body { width: 1200px; height: 866px; overflow: hidden; }
  body {
    background: var(--stage);
    font-family: "Lato", sans-serif;
    display: flex;
    align-items: center;
    justify-content: center;
    gap: 40px;
  }
  .card {
    position: relative;
    width: 540px;
    height: 334px;
    overflow: hidden;
    box-shadow: 0 10px 26px rgba(0,0,0,.45);
  }

  /* Front */
  .card--front { background: var(--paper); color: var(--ink); }
  .contact { position: absolute; left: 34px; top: 36px; }
  .contact__name {
    font-weight: 900; font-size: 18px; color: var(--navy);
    letter-spacing: .5px; text-transform: uppercase; margin-bottom: 3px;
  }
  .contact__role { font-size: 14px; line-height: 1.35; }
  .contact__list { list-style: none; margin-top: 5px; }
  .contact__item {
    display: flex; align-items: center; gap: 8px;
    font-size: 14px; line-height: 1.45; white-space: nowrap;
  }
  .contact__item svg { width: 11px; height: 11px; fill: var(--ink); flex: none; }
  .contact__item--web { color: var(--blue); }
  .contact__item--web svg { fill: var(--blue); }

  .wordmark {
    position: absolute; right: 40px; top: 186px;
    display: flex; align-items: center; gap: 12px;
  }
  .wordmark__dot { width: 16px; height: 16px; background: var(--blue); flex: none; }
  .wordmark__name {
    font-weight: 700; color: var(--ink); text-transform: uppercase;
    display: flex; flex-direction: column; line-height: 1.1;
  }
  .wordmark__main { font-size: 26px; letter-spacing: 4px; }
  .wordmark__sub { font-size: 10.5px; letter-spacing: 2.6px; }

  .address {
    position: absolute; right: 40px; bottom: 36px;
    text-align: right; font-size: 15px; line-height: 1.4;
    letter-spacing: .4px; font-style: normal;
  }
  .edge-band {
    position: absolute; left: 0; right: 0; bottom: 0; height: 12px;
    background: linear-gradient(90deg, var(--navy) 0 30%, var(--sky) 30% 62%, var(--blue) 62% 100%);
  }

  /* Back */
  .card--back {
    background: linear-gradient(135deg, #1d76b6 0%, var(--blue) 45%, var(--sky) 100%);
    color: var(--paper);
    display: flex; align-items: center; justify-content: center;
  }
  .back-mark {
    font-weight: 700; text-transform: uppercase;
    display: flex; flex-direction: column; align-items: center; line-height: 1.15;
  }
  .back-mark__main { font-size: 50px; letter-spacing: 6px; }
  .back-mark__sub { font-size: 18px; letter-spacing: 5px; }
</style>
</head>
<body>
  <article class="card card--front">
    <section class="contact">
      <h1 class="contact__name">Tomas Varenholt</h1>
      <p class="contact__role">Director and Founder</p>
      <p class="contact__role">Certified Accountant</p>
      <ul class="contact__list">
        <li class="contact__item">
          <svg viewBox="0 0 12 12" aria-hidden="true"><path d="M1 4c0-2 2-3 5-3s5 1 5 3v1H8V4H4v1H1zM3 6h6l1 5H2z"/></svg>
          022 418 57 34
        </li>
        <li class="contact__item">
          <svg viewBox="0 0 12 12" aria-hidden="true"><path d="M0 2h12v8H0zM1 3v.4l5 3.4 5-3.4V3z" fill-rule="evenodd"/></svg>
          tv@clairevalconseil.ch
        </li>
        <li class="contact__item contact__item--web">
          <svg viewBox="0 0 12 12" aria-hidden="true"><circle cx="6" cy="6" r="6"/></svg>
          www.clairevalconseil.ch
        </li>
      </ul>
    </section>

    <div class="wordmark">
      <span class="wordmark__dot"></span>
      <span class="wordmark__name">
        <span class="wordmark__main">Claireval</span>
        <span class="wordmark__sub">Conseil et Comptes</span>
      </span>
    </div>

    <address class="address">
      Rue des Vergières 27<br>1201 Geneva
    </address>
    <div class="edge-band"></div>
  </article>

  <article class="card card--back">
    <p class="back-mark">
      <span class="back-mark__main">Claireval</span>
      <span class="back-mark__sub">Conseil et Comptes</span>
    </p>
  </article>
</body>
</html>
```